New Fun, Positive, energised looking Business Card Needed for High Achiever Coach

I am looking for a two sided full colour business card. I am self employed and have recently re branded my 1-2-1 work re-vitalising high achievers. My target client base for these cards is therefore high achievers - usually aged 40 -55, they are often entrepreneurs, CEO or work in banking and finance and 2/3 are male. I work with them on 90 day or 6 month coaching programs to help them live their success in a healthier, more sustainable and fulfiiled way. They pay for this privately so though they are corporate types the cards need not look 'corporate'. I want to portray the idea of transformation, vitality and re-connecting.
You can get a feel for the look I like on my new website: morvenlisk.co.uk
I want to use this logo with strapline (Re-Vitalising High Achievers) (I purchased off Logoharbor) and font/ colours (the turquoise and green).
Details to include on the card:
www.morvenlisk.co.uk
+44 7915 302618
morven@morvenlisk.co.uk
skype: morvenlisk
I'd also like to include:
Do you struggle to switch off? Want to be healthier and feel fitter? Want closer relationships? More clarity over the direction you are headed? I can help you do these things using integrated mind-body techniques. Visit morvenlisk.co.uk TODAY to apply for a FREE Breakthrough session.
BUT if that is too much text for a card I am open to advice/ammendments.
Updates
Thanks for your design - I am considering them. PLease change the wording to :

```html
<!DOCTYPE html>
<html lang="en">
<head>
<meta charset="utf-8">
<title>Morven Lisk – Business Card</title>
<link href="https://fonts.googleapis.com/css2?family=Open+Sans:wght@400;600;700&display=swap" rel="stylesheet">
<style>
  :root {
    --turquoise: #18a3cb;
    --turquoise-deep: #1396bd;
    --green: #5dba4c;
    --ink: #3d4a55;
    --divider: #c9d3d8;
    --paper: #ffffff;
    --backdrop: #eef1f3;
  }
  * { box-sizing: border-box; margin: 0; padding: 0; }
  html, body {
    width: 1200px;
    height: 720px;
    overflow: hidden;
    background: var(--backdrop);
    font-family: "Open Sans", Arial, sans-serif;
  }
  .canvas {
    position: relative;
    width: 1200px;
    height: 720px;
  }
  .card {
    position: absolute;
    top: 205px;
    width: 540px;
    height: 310px;
    overflow: hidden;
    box-shadow: 0 2px 10px rgba(0, 0, 0, 0.12);
  }
  .card--front { left: 40px; background: var(--paper); }
  .card--back  { left: 620px; background: var(--turquoise); }

  /* Front */
  .web-band {
    position: absolute;
    top: 30px;
    left: 0;
    width: 100%;
    height: 46px;
    background: var(--turquoise);
    border-top: 3px solid var(--paper);
    outline: 2px solid var(--green);
    outline-offset: 0;
    display: flex;
    align-items: center;
    justify-content: center;
    color: var(--paper);
    font-weight: 600;
    font-size: 15px;
    letter-spacing: 4px;
  }
  .web-band::before,
  .web-band::after {
    content: "";
    position: absolute;
    left: 0;
    width: 100%;
    height: 2px;
    background: var(--green);
  }
  .web-band::before { top: -9px; }
  .web-band::after  { bottom: -9px; }

  .identity {
    position: absolute;
    top: 92px;
    left: 0;
    width: 270px;
    height: 200px;
    display: flex;
    align-items: center;
    justify-content: center;
  }
  .identity__name {
    color: var(--green);
    font-weight: 700;
    font-size: 30px;
  }
  .divider {
    position: absolute;
    top: 110px;
    left: 270px;
    width: 1px;
    height: 150px;
    background: var(--divider);
  }
  .contacts {
    position: absolute;
    top: 128px;
    left: 292px;
    list-style: none;
  }
  .contacts__item {
    display: flex;
    align-items: center;
    gap: 9px;
    color: var(--ink);
    font-size: 15px;
    height: 36px;
  }
  .contacts__icon {
    width: 16px;
    height: 16px;
    flex: none;
  }

  /* Back */
  .pitch {
    position: absolute;
    inset: 0;
    display: flex;
    flex-direction: column;
    align-items: center;
    justify-content: center;
    text-align: center;
    color: var(--paper);
    font-size: 16px;
    line-height: 1.35;
    gap: 14px;
  }
  .pitch strong { font-weight: 700; }
</style>
</head>
<body>
<main class="canvas">

  <section class="card card--front" aria-label="Business card, front">
    <div class="web-band">www.morvenlisk.co.uk</div>

    <div class="identity">
      <span class="identity__name">Morven Lisk</span>
    </div>

    <div class="divider"></div>

    <ul class="contacts">
      <li class="contacts__item">
        <svg class="contacts__icon" viewBox="0 0 16 16" aria-hidden="true">
          <circle cx="8" cy="8" r="7.2" fill="none" stroke="var(--turquoise)" stroke-width="1.4"/>
          <path d="M5.4 4.2 L6.8 5.9 L6 7 Q7 9 9 10 L10.1 9.2 L11.8 10.6 L10.9 11.8 Q7.8 11.8 5.6 9.4 Q4 7.4 4.2 5.1 Z" fill="var(--turquoise)"/>
        </svg>
        <span>+44 7915 302618</span>
      </li>
      <li class="contacts__item">
        <svg class="contacts__icon" viewBox="0 0 16 16" aria-hidden="true">
          <circle cx="8" cy="8" r="8" fill="var(--turquoise)"/>
          <rect x="3.8" y="5.2" width="8.4" height="5.8" rx="0.6" fill="var(--paper)"/>
          <path d="M3.9 5.4 L8 8.6 L12.1 5.4" fill="none" stroke="var(--turquoise)" stroke-width="1"/>
        </svg>
        <span>morven@morvenlisk.co.uk</span>
      </li>
      <li class="contacts__item">
        <svg class="contacts__icon" viewBox="0 0 16 16" aria-hidden="true">
          <circle cx="8" cy="8" r="8" fill="var(--turquoise)"/>
        </svg>
        <span>morvenlisk</span>
      </li>
    </ul>
  </section>

  <section class="card card--back" aria-label="Business card, back">
    <div class="pitch">
      <p>Do you struggle to switch off?<br>
         Want to be healthier and feel fitter?<br>
         Want closer relationships?<br>
         More clarity over the direction you are headed?</p>
      <p>I can help you do these things using integrated<br>
         mind-body techniques.</p>
      <p>Visit <strong>morvenlisk.co.uk</strong> TODAY to apply for a<br>
         FREE Breakthrough session.</p>
    </div>
  </section>

</main>
</body>
</html>
```